Dietary supplement, Clean and simple.

Hi,
I’d like to talk about the project,

About us:
We are a dietary supplement (Vitamins, Minerals, amino acids etc.) company.
The goal is to have about 25 products at the end of this year. However, for this goal to be achieved we need a good label design to make our products represent our company values.
I’ll be here every day supporting your questions, we are fully committed to making the highest/best quality/customer experience possible.

About the design and our values:
- Professional (We are in the industry of professionalism and expertise. I would love to show we are competent at this, Id. Like to have the labels looks like we have done our research.)
- Efficient (White spacing, good use of the space available.)
- Simple (Straight forward, in 5 seconds they have to know what the product they have is/how functions. We’re trying to simplify it for the consumer.
- No distractions (the only visually “distracting” factor can be the vector art.)

The guidelines:
The goal is to have a universal design, with one element that changes (Vector art). I’ll attach a file/multiple files I think can show some visuals on what I’m looking for, and what parts of the design I think are good/bad.

Label size: 69x155mm (Front is 77.5mm)

Design whatever you think fits our image. You’re the design expert, all I care about is that it fits our company standards/image.

Use this color/font.
Font: Sans Serif
Main company color is Mind green #237D62 (Use this color for something in the design.)

What I thought would be cool/might looks ugly, who knows:
1. The front of the label: Should have 1 vector art, preferably in the top right corner. (That looks good in multiple colors. The vector can have multiple areas to color, I would prefer 2 main colors in the vector art. The interchangeable colors are used for multiple kinds of products.)
2. Text/product information on the left. The text that will have to be displayed:
- Product name for instance “Magnesium + B6”
- Description for the product for instance “Magnesium with ginger taste”
- Company name or logo. (Add ® behind it. We are soon to be trademark registered.)
3. We need to show the "daily intake" amount on the front and also the amount in the complete bottle. For instance, “Daily intake 1 capsule, 60 capsules”.
• You don’t have to design the backside of the label. After I chose a design, I’d like to chat and give specific information on what areas need to be assigned where. (Too complex because of the law.)
Updates

Hi, Please make the deadline 31 days total. I want designers to have the time to design. And not be rushed to finish it.

I want to extend the deadline because i feel like a slightly more medical look would be interesting. Hope you can come up with something!!

Target Market(s)

Dietary supplement consumers

Industry/Entity Type

Dietary supplements

Font styles to use
Sans Serif

Colors

Designer to choose colors to be used in the design.

Requirements
Must have
• Trademark icon "®" has to be at the top right after the company logo(text of logo)/name.

```html
<!DOCTYPE html>
<html lang="en">
<head>
<meta charset="UTF-8">
<title>Magnesium + B6 — Label Set</title>
<link rel="stylesheet" href="https://fonts.googleapis.com/css2?family=Roboto:wght@400;700&family=Roboto+Condensed:wght@400;700&display=swap">
<style>
  :root {
    --page-bg: #ffffff;
    --label-top: #ececec;
    --label-bottom: #d9d9d9;
    --label-edge: #d2d2d2;
    --brand-green: #237d62;
    --ink: #333333;
    --ink-soft: #5a5a5a;
    --accent-red: #e2553f;
    --art-blue-a: rgba(125, 155, 224, 0.55);
    --art-blue-b: rgba(110, 180, 200, 0.55);
    --art-warm-a: rgba(239, 155, 120, 0.5);
    --art-warm-b: rgba(240, 212, 102, 0.5);
    --art-cool-a: rgba(80, 150, 205, 0.45);
    --art-cool-b: rgba(197, 74, 156, 0.45);
  }
  * { margin: 0; padding: 0; box-sizing: border-box; }
  html, body {
    width: 1200px;
    height: 873px;
    overflow: hidden;
    background: var(--page-bg);
  }
  .label-set {
    position: relative;
    width: 1200px;
    height: 873px;
  }
  .label {
    position: absolute;
    width: 300px;
    height: 334px;
    background: linear-gradient(180deg, var(--label-top) 0%, var(--label-bottom) 100%);
    border: 1px solid var(--label-edge);
    overflow: hidden;
    font-family: "Roboto", sans-serif;
    color: var(--ink);
  }
  .label--blue { left: 140px; top: 340px; }
  .label--warm { left: 450px; top: 377px; }
  .label--cool { left: 760px; top: 340px; }

  .label__art {
    position: absolute;
    top: 0;
    right: 0;
    width: 62%;
    height: 100%;
  }
  .label--blue .label__art {
    background: linear-gradient(100deg, rgba(255,255,255,0) 0%, var(--art-blue-a) 55%, var(--art-blue-b) 100%);
  }
  .label--warm .label__art {
    background: linear-gradient(100deg, rgba(255,255,255,0) 0%, var(--art-warm-a) 55%, var(--art-warm-b) 100%);
  }
  .label--cool .label__art {
    background: linear-gradient(100deg, rgba(255,255,255,0) 0%, var(--art-cool-a) 55%, var(--art-cool-b) 100%);
  }

  .brand {
    position: absolute;
    left: 31px;
    top: 100px;
    display: flex;
    align-items: flex-start;
    color: var(--brand-green);
    font-weight: 700;
    line-height: 1;
  }
  .brand__name { font-size: 21px; letter-spacing: 0.3px; }
  .brand__mark { font-size: 9px; margin-left: 2px; }

  .product {
    position: absolute;
    left: 31px;
    top: 196px;
  }
  .product__name {
    font-family: "Roboto Condensed", sans-serif;
    font-weight: 700;
    font-size: 20px;
    letter-spacing: 0.3px;
    line-height: 1;
    color: var(--ink);
  }
  .product__desc {
    margin-top: 5px;
    font-size: 6.5px;
    letter-spacing: 1.6px;
    text-transform: uppercase;
    color: var(--ink-soft);
  }

  .dose {
    position: absolute;
    left: 31px;
    top: 248px;
    font-family: "Roboto Condensed", sans-serif;
  }
  .dose__count { font-weight: 700; font-size: 13px; line-height: 1; }
  .dose__unit { font-size: 5.5px; text-transform: uppercase; color: var(--ink-soft); }
  .dose__rule {
    width: 18px;
    height: 2px;
    background: var(--accent-red);
    margin: 6px 0 6px;
  }
  .dose__intake { font-weight: 700; font-size: 14px; line-height: 1; }
  .dose__note { font-size: 5.5px; text-transform: uppercase; color: var(--ink-soft); }
</style>
</head>
<body>
<main class="label-set">

  <article class="label label--blue">
    <div class="label__art" role="img" aria-label="Line-wave vector art in blue and teal"></div>
    <div class="brand"><span class="brand__name">VERDANT CALM</span><span class="brand__mark">®</span></div>
    <div class="product">
      <h2 class="product__name">MAGNESIUM + B6</h2>
      <p class="product__desc">Magnesium with ginger taste</p>
    </div>
    <div class="dose">
      <p class="dose__count">60</p>
      <p class="dose__unit">Capsules</p>
      <div class="dose__rule"></div>
      <p class="dose__intake">1 CAPSULE</p>
      <p class="dose__note">Daily intake</p>
    </div>
  </article>

  <article class="label label--warm">
    <div class="label__art" role="img" aria-label="Line-wave vector art in orange and yellow with a pink accent"></div>
    <div class="brand"><span class="brand__name">VERDANT CALM</span><span class="brand__mark">®</span></div>
    <div class="product">
      <h2 class="product__name">MAGNESIUM + B6</h2>
      <p class="product__desc">Magnesium with ginger taste</p>
    </div>
    <div class="dose">
      <p class="dose__count">60</p>
      <p class="dose__unit">Capsules</p>
      <div class="dose__rule"></div>
      <p class="dose__intake">1 CAPSULE</p>
      <p class="dose__note">Daily intake</p>
    </div>
  </article>

  <article class="label label--cool">
    <div class="label__art" role="img" aria-label="Line-wave vector art in blue and magenta"></div>
    <div class="brand"><span class="brand__name">VERDANT CALM</span><span class="brand__mark">®</span></div>
    <div class="product">
      <h2 class="product__name">MAGNESIUM + B6</h2>
      <p class="product__desc">Magnesium with ginger taste</p>
    </div>
    <div class="dose">
      <p class="dose__count">60</p>
      <p class="dose__unit">Capsules</p>
      <div class="dose__rule"></div>
      <p class="dose__intake">1 CAPSULE</p>
      <p class="dose__note">Daily intake</p>
    </div>
  </article>

</main>
</body>
</html>
```